We need a business card design for a new company located in Brampton Ontario Canada. Our goal is to promote companies to use our service as an "External Program Management " firm taking their industrial product concepts " from prototype to production." We would like to use blue and yellow as our colors. Our skills include finding suppliers for prototype parts and developing them into supplying not only prototypes but the final production parts as well for our customer base.
Industry/Entity Type
Business
Contact Information for Business Card
Derek Namsby
Sales Manager
KOLVEN Solutions Inc.
14 Pinemarsh Lane
Brampton, Ontario L7P 2K9
Canada
Phone: 905-481-2976
Fax: 905-481-2976
website: www.kolvensolutions-example.com
Email: derek@kolvensolutions-example.com
Look and feel
Each slider illustrates characteristics of the customer's brand and the style your logo design should communicate.

```html
<!DOCTYPE html>
<html lang="en">
<head>
<meta charset="utf-8">
<title>KOLVEN Solutions Inc. – Business Card</title>
<link rel="stylesheet" href="https://fonts.googleapis.com/css2?family=Saira:wght@400;500;600&display=swap">
<style>
  :root {
    --page-bg: #e9e9ec;
    --card-bg: #ffffff;
    --brand-blue: #1f1fd6;
    --deep-blue: #20209a;
    --accent-yellow: #f5c518;
    --text-dark: #3a3a40;
    --rule: #55555c;
    --white: #ffffff;
  }
  * { margin: 0; padding: 0; box-sizing: border-box; }
  html, body { width: 1200px; height: 900px; overflow: hidden; }
  body {
    background: var(--page-bg);
    font-family: "Saira", sans-serif;
    position: relative;
  }
  .business-card {
    position: absolute;
    left: 100px; top: 165px;
    width: 1000px; height: 570px;
    background: var(--card-bg);
    overflow: hidden;
    box-shadow: 0 6px 24px rgba(0,0,0,0.12);
  }
  .card-waves { position: absolute; inset: 0; width: 1000px; height: 570px; }
  .wordmark {
    position: absolute;
    left: 70px; top: 175px;
    color: var(--deep-blue);
    font-weight: 600;
    line-height: 1;
  }
  .wordmark-main { display: block; font-size: 86px; letter-spacing: 2px; }
  .wordmark-sub { display: block; font-size: 44px; margin-top: 4px; }
  .divider {
    position: absolute;
    left: 585px; top: 70px;
    width: 2px; height: 250px;
    background: var(--rule);
  }
  .contact-block {
    position: absolute;
    left: 605px; top: 68px;
    color: var(--text-dark);
  }
  .person-name {
    color: var(--brand-blue);
    font-size: 25px; font-weight: 500;
    letter-spacing: 1px; line-height: 1.1;
  }
  .person-title { font-size: 17px; margin-bottom: 18px; }
  .address { font-size: 17px; line-height: 1.35; margin-bottom: 18px; }
  .contact-list { list-style: none; font-size: 15px; }
  .contact-list li { display: flex; align-items: center; gap: 10px; height: 27px; }
  .contact-list svg { width: 15px; height: 15px; fill: var(--deep-blue); flex: none; }
  .website {
    position: absolute;
    right: 40px; bottom: 78px;
    color: var(--white);
    font-size: 20px; letter-spacing: 0.5px;
  }
</style>
</head>
<body>
  <main class="business-card">
    <svg class="card-waves" viewBox="0 0 1000 570" aria-hidden="true">
      <path fill="var(--accent-yellow)" d="M0,468 C300,480 560,440 770,360 C600,470 320,508 0,508 Z"/>
      <path fill="var(--brand-blue)" d="M0,522 C330,532 680,470 1000,300 V570 H0 Z"/>
    </svg>

    <div class="wordmark">
      <span class="wordmark-main">KOLVEN</span>
      <span class="wordmark-sub">Solutions Inc.</span>
    </div>

    <div class="divider"></div>

    <section class="contact-block">
      <p class="person-name">DEREK NAMSBY</p>
      <p class="person-title">Sales Manager</p>
      <p class="address">14 Pinemarsh Lane<br>Brampton, ON L7P 2K9</p>
      <ul class="contact-list">
        <li>
          <svg viewBox="0 0 16 16"><path d="M3.5 1l2.5 3-1.5 2c1 2 3 4 5 5l2-1.5 3 2.5-1.5 2.5C7 15 1 9 1 2.5z"/></svg>
          905-481-2976
        </li>
        <li>
          <svg viewBox="0 0 16 16"><path d="M4 0h8v16H4z M5.5 2v10h5V2z"/></svg>
          905-481-2976
        </li>
        <li>
          <svg viewBox="0 0 16 16"><path d="M4 1h7v4H4z M1 6h14v9H1z M4 10h8v2H4z"/></svg>
          905-481-2976
        </li>
        <li>
          <svg viewBox="0 0 16 16"><path d="M0 3h16v10H0z M1.5 4.2L8 9l6.5-4.8" stroke="#fff" stroke-width="1"/></svg>
          derek@kolvensolutions-example.com
        </li>
      </ul>
    </section>

    <p class="website">www.kolvensolutions-example.com</p>
  </main>
</body>
</html>
```